ALL TYPES OF COMMERCIAL PLASTERING

TYPE OF BLOCK LETTERING WITH STAND OUT QUALITIES
WITH SOME TYPE OF LOGO
SOMETHING UNIQUE FOR THE BUILDING INDUSTRY.
QUALITY WORKMANSHIP
Updates

forgot to include my mobile phone number on my brief. could you add it to your design please MOBILE PH 0491 586 032

please let me make this quite clear ,the company name is harbourline linings and Fitouts PTY LTD. THE TYPE OF WORK WE WILL BE DOING IS COMMERCIAL PLASTERING.

Industry/Entity Type

Industry

Contact Information for Business Card

harbourline linings and fitouts P/L
marcus trelawny p.o.box 82 wendouree 3355 email address harbourlinelinings@mailcove.example
ABN 84 519 263 740 COMMERCIAL PLASTERING

```html
<!DOCTYPE html>
<html lang="en">
<head>
<meta charset="utf-8">
<title>Harbourline Linings and Fitouts – Business Card</title>
<link href="https://fonts.googleapis.com/css2?family=Arimo:wght@400;700&display=swap" rel="stylesheet">
<style>
  :root{
    --lime:#b3d235;
    --ink:#0b0b0b;
    --paper:#ffffff;
    --shade:#9a9a9a;
    --backdrop:#e8e8e4;
  }
  *{margin:0;padding:0;box-sizing:border-box}
  html,body{width:1200px;height:848px;overflow:hidden;background:var(--backdrop)}
  body{position:relative;font-family:"Arimo",Arial,sans-serif}
  .card{
    position:absolute;left:100px;top:138px;width:1000px;height:572px;
    background:var(--paper);border-radius:34px;overflow:hidden;
    box-shadow:0 10px 30px rgba(0,0,0,.18);
  }
  .card svg{position:absolute;left:0;top:0}
  .brand{
    position:absolute;left:590px;top:44px;width:390px;
    display:flex;align-items:center;gap:14px;
  }
  .brand-dot{
    flex:0 0 auto;width:58px;height:58px;border-radius:50%;
    border:6px solid var(--lime);
  }
  .brand-name{
    color:var(--lime);font-weight:700;font-size:23px;line-height:1.08;
    text-transform:uppercase;letter-spacing:.5px;
  }
  .tagline{
    position:absolute;left:662px;top:122px;color:var(--paper);
    font-size:15px;letter-spacing:1px;text-transform:uppercase;
  }
  .holder{
    position:absolute;left:500px;top:190px;color:var(--paper);
    font-size:34px;font-weight:400;letter-spacing:.3px;
  }
  .contacts{position:absolute;left:470px;top:268px;list-style:none}
  .contacts li{
    display:flex;align-items:center;gap:22px;height:44px;
    color:var(--paper);font-size:25px;letter-spacing:.2px;
  }
  .contacts svg{position:static;flex:0 0 24px}
</style>
</head>
<body>
  <div class="card">
    <svg width="1000" height="572" viewBox="0 0 1000 572" role="img" aria-label="Faint grey illustration of a plasterer holding a hawk and trowel">
      <defs>
        <radialGradient id="figureWash" cx="0.5" cy="0.5" r="0.5">
          <stop offset="0" stop-color="#9a9a9a" stop-opacity=".55"/>
          <stop offset="1" stop-color="#9a9a9a" stop-opacity="0"/>
        </radialGradient>
      </defs>
      <ellipse cx="250" cy="310" rx="260" ry="300" fill="url(#figureWash)"/>
    </svg>
    <svg width="1000" height="572" viewBox="0 0 1000 572" aria-hidden="true">
      <path class="arc-lime" d="M540,0 C390,70 320,250 350,410 C368,490 410,545 445,572 L1000,572 L1000,0 Z" fill="var(--lime)"/>
      <path class="panel-black" d="M590,0 C440,80 370,255 398,410 C414,490 455,545 490,572 L1000,572 L1000,0 Z" fill="var(--ink)"/>
    </svg>

    <div class="brand">
      <span class="brand-dot"></span>
      <span class="brand-name">harbourline linings and fitouts P/L</span>
    </div>
    <div class="tagline">Commercial Plastering</div>

    <div class="holder">marcus trelawny</div>

    <ul class="contacts">
      <li>
        <svg width="24" height="26" viewBox="0 0 24 26" aria-hidden="true"><rect x="5" y="1" width="14" height="24" rx="2" fill="none" stroke="var(--lime)" stroke-width="2.5"/><rect x="8" y="5" width="8" height="8" fill="var(--lime)"/></svg>
        0491 586 032
      </li>
      <li>
        <svg width="24" height="26" viewBox="0 0 24 26" aria-hidden="true"><path d="M12 25 C5 16 3 12 3 9 A9 9 0 0 1 21 9 C21 12 19 16 12 25 Z" fill="none" stroke="var(--lime)" stroke-width="2.5"/><circle cx="12" cy="9" r="3" fill="var(--lime)"/></svg>
        ABN 84 519 263 740
      </li>
      <li>
        <svg width="24" height="24" viewBox="0 0 24 24" aria-hidden="true"><path d="M12 2 L23 12 H19 V22 H14 V15 H10 V22 H5 V12 H1 Z" fill="var(--lime)"/></svg>
        p.o.box 82 wendouree 3355
      </li>
      <li>
        <svg width="24" height="18" viewBox="0 0 24 18" aria-hidden="true"><rect x="1" y="1" width="22" height="16" fill="var(--lime)"/><path d="M1 1 L12 10 L23 1" fill="none" stroke="var(--ink)" stroke-width="2"/></svg>
        harbourlinelinings@mailcove.example
      </li>
    </ul>
  </div>
</body>
</html>
```